Design the 21st Harborlight Open Cinema Showcase Poster. Think modern, chic, cool, film, movies - driving people to the film festival - the film festivla is in San Francisco and the SF East Bay. Our logo is attached. Dates will be determined soon . please use - November 2 - 11, 2018 (for placement) Keep in mind abstract, chic, modern - eye catching. website is www.hlocs-fest.org

Target Market(s)

25 - 45 year old - upper middle class

Industry/Entity Type

Film Production

Colors

Designer to choose colors to be used in the design.

Requirements
Must have
• logo (attached) www.hlocs-fest.org - chic modern design
Nice to have
• best coolest poster ever!
Should not have
• CLIP ART!!!

```html
<!DOCTYPE html>
<html lang="en">
<head>
<meta charset="utf-8">
<title>21st Harborlight Open Cinema Showcase — November 2 – 11, 2018</title>
<link rel="stylesheet" href="https://fonts.googleapis.com/css2?family=Josefin+Sans:wght@300&family=Permanent+Marker&display=swap">
<style>
  :root {
    --bg: #2b2b2b;
    --ink: #f4f4f4;
    --ink-soft: #d9d9d9;
    --title-ink: #ededed;
  }
  * { margin: 0; padding: 0; box-sizing: border-box; }
  html, body {
    width: 849px; height: 1200px; overflow: hidden;
    background: var(--bg);
  }
  .poster {
    position: relative;
    width: 849px; height: 1200px;
    background: var(--bg);
    font-family: "Josefin Sans", sans-serif;
    font-weight: 300;
    color: var(--ink);
  }
  .poster__frame, .poster__glows {
    position: absolute; inset: 0;
  }
  .poster__title {
    position: absolute;
    left: 96px; top: 112px;
    width: 600px;
    font-family: "Permanent Marker", cursive;
    font-weight: 400;
    color: var(--title-ink);
    text-transform: uppercase;
    transform: rotate(-6deg);
    transform-origin: left top;
  }
  .poster__title-line {
    display: block;
    font-size: 78px;
    line-height: 118px;
    letter-spacing: 1px;
    white-space: nowrap;
  }
  .poster__title-edition {
    font-size: 74px;
    line-height: 100px;
  }
  .poster__title-edition sup {
    font-size: 34px;
    vertical-align: 32px;
    margin-left: 4px;
  }
  .poster__title-line--fade {
    color: #d6d6d6;
  }
  .poster__details {
    position: absolute;
    left: 108px; top: 883px;
    padding-left: 22px;
    border-left: 4px solid var(--ink);
    height: 146px;
  }
  .poster__dates {
    font-size: 41px;
    letter-spacing: -0.5px;
    line-height: 1;
    margin-bottom: 26px;
  }
  .poster__venue {
    font-size: 25px;
    line-height: 1.55;
    letter-spacing: -0.3px;
    color: var(--ink-soft);
  }
  .poster__website {
    position: absolute;
    left: 50%; top: 1143px;
    transform: translateX(-50%);
    padding: 0 10px;
    background: var(--bg);
    font-size: 21px;
    letter-spacing: 0.5px;
    color: var(--ink-soft);
  }
</style>
</head>
<body>
<main class="poster">
  <svg class="poster__glows" width="849" height="1200" viewBox="0 0 849 1200" aria-hidden="true">
    <defs>
      <radialGradient id="glow-large">
        <stop offset="0" stop-color="#ff2a3a"/>
        <stop offset="0.12" stop-color="#d8232f"/>
        <stop offset="0.35" stop-color="#5d4a55" stop-opacity="0.8"/>
        <stop offset="0.7" stop-color="#3a3d44" stop-opacity="0.5"/>
        <stop offset="1" stop-color="#2b2b2b" stop-opacity="0"/>
      </radialGradient>
      <radialGradient id="glow-top">
        <stop offset="0" stop-color="#ff2a3a"/>
        <stop offset="0.18" stop-color="#d8232f"/>
        <stop offset="0.5" stop-color="#4b4a3c" stop-opacity="0.6"/>
        <stop offset="1" stop-color="#2b2b2b" stop-opacity="0"/>
      </radialGradient>
      <radialGradient id="glow-small">
        <stop offset="0" stop-color="#ff2a3a"/>
        <stop offset="0.25" stop-color="#d8232f"/>
        <stop offset="0.6" stop-color="#5a5a5e" stop-opacity="0.5"/>
        <stop offset="1" stop-color="#2b2b2b" stop-opacity="0"/>
      </radialGradient>
    </defs>
    <circle cx="527" cy="491" r="210" fill="url(#glow-large)"/>
    <circle cx="627" cy="199" r="85" fill="url(#glow-top)"/>
    <circle cx="610" cy="667" r="45" fill="url(#glow-small)"/>
  </svg>

  <h1 class="poster__title">
    <span class="poster__title-line poster__title-edition">21<sup>st</sup></span>
    <span class="poster__title-line">Harborlight</span>
    <span class="poster__title-line">Open Cinema</span>
    <span class="poster__title-line poster__title-line--fade">Showcase</span>
  </h1>

  <svg class="poster__frame" width="849" height="1200" viewBox="0 0 849 1200" aria-hidden="true">
    <rect x="44" y="32" width="781" height="1128" rx="22" fill="none" stroke="#f4f4f4" stroke-width="3.5"/>
  </svg>

  <section class="poster__details">
    <p class="poster__dates">NOVEMBER 2 - 11, 2018</p>
    <p class="poster__venue">SF EAST BAY</p>
    <p class="poster__venue">SAN FRANCISCO</p>
  </section>

  <p class="poster__website">WWW.HLOCS-FEST.ORG</p>
</main>
</body>
</html>
```